WordPress Site That Reviews Footwear

We need a wordpress web design for an affiliate site called PaceKite. We review and do roundups on footwear products. The final design should be clean and mobile friendly. The site should be built with Gutenberg page builder. We like the design of https://lunavessel.com/.
Updates

Need extra days to review

Target Market(s)

USA

Industry/Entity Type

Footwear

Logo Text

PaceKite

Number of Pages Required

4 page

Font styles to use
Serif
Sans Serif

Requirements
Must have
• Wordpress site
Blog post
Page
Categories
Homepage

```html
<!DOCTYPE html>
<html lang="en">
<head>
<meta charset="utf-8">
<title>PaceKite – Footwear Reviews</title>
<link href="https://fonts.googleapis.com/css2?family=Alfa+Slab+One&family=Montserrat:wght@400;500;600;700&family=Roboto:wght@400;500;700&display=swap" rel="stylesheet">
<style>
:root{
  --yellow:#ffd000;
  --hero-yellow:#fee152;
  --ink:#262626;
  --text:#4a4a4a;
  --muted:#666;
  --cream:#fff8db;
  --panel:#1c1c1c;
  --gray-bg:#ebebeb;
  --footer-bg:#f4f4f4;
}
*{margin:0;padding:0;box-sizing:border-box}
html,body{width:1200px;height:3504px;overflow:hidden}
body{position:relative;background:#fff;font-family:'Montserrat',sans-serif;color:var(--text)}
.abs{position:absolute}
.slab{font-family:'Alfa Slab One',serif;color:var(--ink);font-weight:400}

/* header */
.follow{left:248px;top:41px;font-size:14px;font-weight:600;color:var(--ink)}
.social-dot{width:30px;height:30px;border-radius:50%;background:var(--ink)}
.social-dot.first{background:var(--yellow)}
.brand{left:528px;top:30px;font-family:'Alfa Slab One',serif;font-size:27px;color:var(--ink)}
.call-label{left:796px;top:33px;font-size:14px;font-weight:500;color:var(--ink)}
.call-number{left:796px;top:52px;font-size:21px;font-weight:600;color:var(--ink)}
.nav{top:104px;font-size:14.5px;font-weight:600;color:var(--ink);transform:translateX(-50%);white-space:nowrap}
.nav.active{color:var(--yellow)}
.nav-marker{left:308px;top:133px;width:0;height:0;border-left:9px solid transparent;border-right:9px solid transparent;border-bottom:15px solid #000}

/* hero */
.hero{left:0;top:150px;width:1200px;height:598px;background:var(--hero-yellow)}
.hero-photo{left:80px;top:150px;width:400px;height:598px;background:linear-gradient(160deg,#e9e9e9 0%,#b5b5b5 35%,#6f6c66 70%,#55524c 100%);opacity:.9}
.hero-shoes{left:925px;top:600px;width:275px;height:148px;background:radial-gradient(ellipse at 60% 60%,#f4d23a 0%,#f7dc55 60%,rgba(254,225,82,0) 100%)}
.hero-title{left:755px;top:355px;transform:translateX(-50%);font-size:66px;white-space:nowrap}
.hero-text{left:552px;top:442px;width:408px;text-align:center;font-size:13.5px;line-height:22.5px;color:var(--ink)}
.btn-dark{left:678px;top:503px;width:153px;height:41px;border-radius:21px;background:var(--ink);color:#fff;font-size:12px;font-weight:700;display:flex;align-items:center;justify-content:center;letter-spacing:.3px}
.dot{top:676px;width:11px;height:11px;border-radius:50%;background:#fff}
.dot.on{background:var(--ink)}

/* welcome */
.welcome-kicker{left:112px;top:849px;font-size:14px;letter-spacing:5px;color:var(--ink)}
.welcome-brand{left:112px;top:872px;font-size:36px}
.body-copy{font-size:13.5px;line-height:22.4px;color:var(--muted)}
.welcome-copy{left:112px;top:928px;width:470px}
.btn-yellow{left:110px;top:1109px;width:155px;height:42px;border-radius:21px;background:var(--yellow);color:var(--ink);font-size:12px;font-weight:700;display:flex;align-items:center;justify-content:center}
.feature-circle{width:103px;height:103px;border-radius:50%;background:var(--yellow);border:6px solid var(--ink);transform:translate(-50%,-50%)}
.feature-circle::after{content:"";position:absolute;inset:17px;border-radius:50%;background:var(--ink)}
.feature-label{transform:translateX(-50%);font-size:19px;font-weight:600;color:var(--muted);white-space:nowrap}

/* footwear section */
.footwear{left:0;top:1252px;width:1200px;height:816px;background:linear-gradient(180deg,#e4e4e4 0%,#f0f0f0 40%,#f7f7f7 100%)}
.section-title{left:600px;transform:translateX(-50%);font-size:40px;white-space:nowrap;text-align:center;line-height:44px}
.section-copy{left:275px;width:650px;text-align:center;font-size:13.5px;line-height:22.4px;color:var(--ink)}
.dark-panel{left:-4px;top:1480px;width:673px;height:487px;background:linear-gradient(135deg,#2a2a2a,#141414);border:3px solid var(--yellow);border-left:none;border-radius:0 55px 55px 0}
.panel-icon{width:58px;height:58px;border-radius:10px;background:var(--yellow)}
.panel-title{font-size:19px;color:#fff;font-weight:500}
.panel-copy{font-size:13.5px;line-height:23px;color:#fff;width:210px}
.video{left:600px;top:1552px;width:489px;height:344px;background:linear-gradient(120deg,#3d6a4b 0%,#8a8a88 35%,#e3dfd9 60%,#c94a3c 85%,#6b5a4a 100%);border:1px solid #555}
.play{left:808px;top:1686px;width:76px;height:76px;border-radius:50%;background:var(--yellow);display:flex;align-items:center;justify-content:center}

/* advice cards */
.card{top:2360px;width:313px;height:207px;border-radius:24px;background:var(--cream);padding:40px 40px 0}
.card.raised{box-shadow:0 6px 18px rgba(0,0,0,.12)}
.card h3{font-size:19px;font-weight:500;color:var(--ink);margin-bottom:12px}
.card p{font-size:13.5px;line-height:22.4px;color:var(--muted)}
.underlined{text-decoration:underline;text-decoration-color:var(--yellow);text-decoration-thickness:2px;text-underline-offset:5px}

/* banner */
.banner{left:0;top:2667px;width:1200px;height:444px;background:radial-gradient(ellipse 280px 230px at 900px 220px,#b3692f 0%,#a45f2d 45%,rgba(200,170,140,0) 100%),linear-gradient(180deg,#e2e2e2 0%,#dcdcdc 75%,#c7ccd2 100%)}
.banner-text{left:112px;top:2765px;font-size:38px;line-height:43px}

/* footer */
.footer{left:0;top:3111px;width:1200px;height:338px;background:var(--footer-bg)}
.foot-head{top:3193px;font-family:'Roboto',sans-serif;font-size:14px;font-weight:700;color:var(--ink);text-decoration:underline;text-underline-offset:3px}
.foot-list{list-style:none;font-family:'Roboto',sans-serif;font-size:14px;color:var(--muted)}
.foot-list li{height:37px;display:flex;align-items:flex-start;gap:12px}
.foot-list .mark{width:10px;color:var(--muted);font-size:13px}
.foot-social{top:3223px;width:31px;height:31px;border-radius:50%;border:2px solid var(--ink)}
.newsletter{left:778px;top:3337px;width:311px;height:48px;background:#fff;border:1px solid #ddd;display:flex;align-items:center;padding-left:17px;font-family:'Roboto',sans-serif;font-size:14px;color:var(--muted)}
.send{left:1042px;top:3340px;width:44px;height:42px;background:var(--yellow);display:flex;align-items:center;justify-content:center}
.bottom-bar{left:0;top:3449px;width:1200px;height:55px;background:var(--yellow);display:flex;align-items:center;justify-content:center;font-family:'Roboto',sans-serif;font-size:14px;color:var(--ink)}
</style>
</head>
<body>

<!-- Header -->
<header>
  <div class="abs follow">Follow us :</div>
  <div class="abs social-dot first" style="left:347px;top:35px"></div>
  <div class="abs social-dot" style="left:381px;top:35px"></div>
  <div class="abs social-dot" style="left:414px;top:35px"></div>
  <div class="abs social-dot" style="left:448px;top:35px"></div>
  <div class="abs brand">PaceKite</div>
  <svg class="abs" style="left:740px;top:33px" width="44" height="44" viewBox="0 0 24 24" aria-hidden="true"><path fill="none" stroke="#ffd000" stroke-width="1.8" d="M6.6 3.5l3 3.2-1.8 2.3c1.2 2.5 3.2 4.6 5.8 5.9l2.2-1.9 3.3 2.9-1.6 2.6c-.4.6-1.1.9-1.8.8C9.7 18.6 5.2 14 4.4 7.9c-.1-.7.2-1.4.8-1.8z"/><path fill="none" stroke="#ffd000" stroke-width="1.6" d="M14 3.5a6.5 6.5 0 0 1 6.5 6.5M14 6.5a3.5 3.5 0 0 1 3.5 3.5"/></svg>
  <div class="abs call-label">Call us Today :</div>
  <div class="abs call-number">+1 888 888 8888</div>
  <nav>
    <div class="abs nav active" style="left:318px">HOME</div>
    <div class="abs nav" style="left:422px">PRODUCTS</div>
    <div class="abs nav" style="left:522px">BLOG</div>
    <div class="abs nav" style="left:616px">REVIEWS</div>
    <div class="abs nav" style="left:728px">ABOUT US</div>
    <div class="abs nav" style="left:853px">CONTACT US</div>
  </nav>
  <div class="abs nav-marker"></div>
</header>

<!-- Hero -->
<section>
  <div class="abs hero"></div>
  <div class="abs hero-photo" role="img" aria-label="Photo of legs in grey trousers wearing white and grey high-top sneakers, raised upward"></div>
  <div class="abs hero-shoes" role="img" aria-label="Pair of yellow slip-on shoes in the corner"></div>
  <h1 class="abs slab hero-title">PaceKite</h1>
  <p class="abs hero-text">Lorem ipsum dolor sit amet, consectetur adipiscing elit, sed do eiusmod tempor incididunt ut labore et</p>
  <div class="abs btn-dark">GET STARTED</div>
  <div class="abs dot on" style="left:609px"></div>
  <div class="abs dot" style="left:625px"></div>
  <div class="abs dot" style="left:641px"></div>
</section>

<!-- Welcome -->
<section>
  <div class="abs welcome-kicker">WELCOME TO</div>
  <h2 class="abs slab welcome-brand">PaceKite</h2>
  <svg class="abs" style="left:60px;top:912px" width="140" height="20" viewBox="0 0 140 20" aria-hidden="true"><path d="M2 16 C40 8 90 4 138 3" fill="none" stroke="#ffd000" stroke-width="2"/></svg>
  <p class="abs body-copy welcome-copy">Lorem ipsum dolor sit amet, consectetur adipiscing elit, sed do eiusmod tempor incididunt ut labore et dolore magna aliqua. Ut enim ad minim veniam, quis nostrud exercitation ullamco laboris nisi ut aliquip ex ea commodo consequat. Duis aute irure dolor in reprehenderit in voluptate velit esse cillum dolore eu fugiat nulla pariatur. Excepteur sint occaecat cupidatat non proident, sunt in culpa qui officia deserunt mollit anim id est laborum.</p>
  <div class="abs btn-yellow">LEARN MORE</div>

  <div class="abs feature-circle" style="left:682px;top:901px" role="img" aria-label="Shoe category icon"></div>
  <div class="abs feature-circle" style="left:844px;top:901px" role="img" aria-label="Sandal category icon"></div>
  <div class="abs feature-circle" style="left:1007px;top:901px" role="img" aria-label="Foot fitting icon"></div>
  <div class="abs feature-circle" style="left:682px;top:1064px" role="img" aria-label="Slipper category icon"></div>
  <div class="abs feature-circle" style="left:844px;top:1064px" role="img" aria-label="Sneaker category icon"></div>
  <div class="abs feature-circle" style="left:1007px;top:1064px" role="img" aria-label="Casual shoe icon"></div>
  <div class="abs feature-label" style="left:682px;top:961px">Lorem ipsum</div>
  <div class="abs feature-label" style="left:844px;top:961px">Lorem ipsum</div>
  <div class="abs feature-label" style="left:1007px;top:961px">Lorem ipsum</div>
  <div class="abs feature-label" style="left:682px;top:1124px">Lorem ipsum</div>
  <div class="abs feature-label" style="left:844px;top:1124px">Lorem ipsum</div>
  <div class="abs feature-label" style="left:1007px;top:1124px">Lorem ipsum</div>
</section>

<!-- What's your footwear -->
<section>
  <div class="abs footwear"></div>
  <h2 class="abs slab section-title" style="top:1350px">What’s <span class="underlined">your</span> footwear</h2>
  <p class="abs section-copy" style="top:1412px">Lorem ipsum dolor sit amet, consectetur adipiscing elit, sed do eiusmod tempor incididunt ut labore et dolore magna aliqua.</p>
  <div class="abs dark-panel"></div>

  <div class="abs panel-icon" style="left:112px;top:1539px" role="img" aria-label="Running shoe icon"></div>
  <div class="abs panel-title" style="left:110px;top:1610px"><span class="underlined">Nemo</span> enim ipsam</div>
  <p class="abs panel-copy" style="left:110px;top:1643px">Lorem ipsum dolor sit amet, consectetur adipiscing</p>

  <div class="abs panel-icon" style="left:376px;top:1539px" role="img" aria-label="Customer icon"></div>
  <div class="abs panel-title" style="left:375px;top:1610px"><span class="underlined">Nemo</span> enim ipsam</div>
  <p class="abs panel-copy" style="left:376px;top:1643px">Lorem ipsum dolor sit amet, consectetur adipiscing</p>

  <div class="abs panel-icon" style="left:112px;top:1738px" role="img" aria-label="Reviewer icon"></div>
  <div class="abs panel-title" style="left:110px;top:1815px"><span class="underlined">Nemo</span> enim ipsam</div>
  <p class="abs panel-copy" style="left:110px;top:1849px">Lorem ipsum dolor sit amet, consectetur adipiscing</p>

  <div class="abs panel-icon" style="left:376px;top:1738px" role="img" aria-label="Fast shipping shoe icon"></div>
  <div class="abs panel-title" style="left:375px;top:1815px"><span class="underlined">Nemo</span> enim ipsam</div>
  <p class="abs panel-copy" style="left:376px;top:1849px">Lorem ipsum dolor sit amet, consectetur adipiscing</p>

  <div class="abs video" role="img" aria-label="Video still of a woman in a green dress trying on nude heels beside a shoe rack"></div>
  <div class="abs play"><svg width="30" height="30" viewBox="0 0 24 24" aria-hidden="true"><path d="M7 4l13 8-13 8z" fill="#1c1c1c"/></svg></div>
</section>

<!-- Footwear advice -->
<section>
  <h2 class="abs slab section-title" style="top:2167px">Finally… Footwear advice<br>that <span class="underlined">gets results</span>.</h2>
  <p class="abs section-copy" style="top:2275px">Lorem ipsum dolor sit amet, consectetur adipiscing elit, sed do eiusmod tempor incididunt ut labore et dolore magna aliqua.</p>
  <article class="abs card" style="left:112px">
    <h3><span class="underlined">Nemo</span> enim ipsam</h3>
    <p>Lorem ipsum dolor sit amet, conse ctetur adipiscing elit, sed do eiusm od tempor incididunt ut labore et dolore magna aliqua.</p>
  </article>
  <article class="abs card raised" style="left:444px">
    <h3><span class="underlined">Nemo</span> enim ipsam</h3>
    <p>Lorem ipsum dolor sit amet, conse ctetur adipiscing elit, sed do eiusm od tempor incididunt ut labore et dolore magna aliqua.</p>
  </article>
  <article class="abs card" style="left:776px">
    <h3><span class="underlined">Nemo</span> enim ipsam</h3>
    <p>Lorem ipsum dolor sit amet, conse ctetur adipiscing elit, sed do eiusm od tempor incididunt ut labore et dolore magna aliqua.</p>
  </article>
</section>

<!-- Banner -->
<section>
  <div class="abs banner" role="img" aria-label="Photo of tan suede desert boots standing among pebbles on a pale surface"></div>
  <h2 class="abs slab banner-text">Lorem ipsum dolor sit amet,<br>consectetur adipiscing elit,<br>sed do eiusmod tempor incididunt ut<br><span class="underlined">labore et</span> dolore magna aliqua.</h2>
</section>

<!-- Footer -->
<footer>
  <div class="abs footer"></div>
  <div class="abs foot-head" style="left:110px">QUICK LINKS</div>
  <ul class="abs foot-list" style="left:110px;top:3229px">
    <li><span class="mark">»</span>Home</li>
    <li><span class="mark">»</span>About Us</li>
    <li><span class="mark">»</span>Our Products</li>
    <li><span class="mark">»</span>Reviews</li>
    <li><span class="mark">»</span>Latest Blog</li>
  </ul>
  <div class="abs foot-head" style="left:295px">OTHER LINKS</div>
  <ul class="abs foot-list" style="left:295px;top:3229px">
    <li><span class="mark">»</span>Terms &amp; Conditions</li>
    <li><span class="mark">»</span>Privacy Policy</li>
    <li><span class="mark">»</span>Help Service</li>
    <li><span class="mark">»</span>FAQ</li>
    <li><span class="mark">»</span>Contact us</li>
  </ul>
  <div class="abs foot-head" style="left:527px">FIND US ON</div>
  <ul class="abs foot-list" style="left:527px;top:3229px">
    <li><svg class="mark" width="10" height="14" viewBox="0 0 10 14" aria-hidden="true"><path d="M5 0a5 5 0 0 0-5 5c0 4 5 9 5 9s5-5 5-9a5 5 0 0 0-5-5zm0 7a2 2 0 1 1 0-4 2 2 0 0 1 0 4z" fill="#666"/></svg><span style="margin-left:8px">201 , Maple Crest Road</span></li>
    <li><span class="mark"></span><span style="margin-left:8px">United States</span></li>
    <li><svg class="mark" width="12" height="12" viewBox="0 0 24 24" aria-hidden="true"><path d="M6.6 2l4 4-2.4 3c1.5 3 3.8 5.3 6.8 6.8l3-2.4 4 4-2.6 3.2C11 20 4 13 2.4 4.6z" fill="#666"/></svg><span style="margin-left:8px">1 888 888 888</span></li>
    <li><svg class="mark" width="13" height="11" viewBox="0 0 26 20" aria-hidden="true"><rect x="1" y="1" width="24" height="18" fill="none" stroke="#666" stroke-width="2"/><path d="M1 1l12 10L25 1" fill="none" stroke="#666" stroke-width="2"/></svg><span style="margin-left:8px">info@companyname.com</span></li>
  </ul>
  <div class="abs foot-head" style="left:778px">CONNECTED US ON</div>
  <div class="abs foot-social" style="left:779px"></div>
  <div class="abs foot-social" style="left:819px"></div>
  <div class="abs foot-social" style="left:859px"></div>
  <div class="abs foot-social" style="left:899px"></div>
  <div class="abs foot-social" style="left:939px"></div>
  <div class="abs foot-head" style="left:778px;top:3295px">SUBSCRIBE TO OUR NEWSLETTER</div>
  <div class="abs newsletter">Email Address</div>
  <div class="abs send"><svg width="20" height="20" viewBox="0 0 24 24" aria-hidden="true"><path d="M22 2L2 10l8 3 3 8z" fill="#1c1c1c"/></svg></div>
  <div class="abs bottom-bar">© 2021 Company name. All Rights Reserved</div>
</footer>

</body>
</html>
```